Letter design, envelope design, and more

Hello, we the Tavrin Gmbh are looking for our shop. Letter C5. Design does not have to be like a business card, so it can have straight lines. Only the color is important. The logo is the text under TaVRin omit.It should not be playful but Profesionel

Font styles to use
Sans Serif

Colors
0555a3
3176b5
85abd2
85cae6
34a7d8
0792cd
cee9f5
cfdfed
000000

Requirements
Must have
• Color like business card, Please, with the text under TaVRin, Correct address Lindmattstr. 4 Zip code 9517 Seewil, as well as Couvert Without addressing only design and logo with TaVrn
Nice to have
• more writing articles
Should not have
• Not too colored, Text under TaVRin, bright colors

```html
<!DOCTYPE html>
<html lang="en">
<head>
<meta charset="utf-8">
<title>Tavrin Gmbh – Stationery</title>
<link href="https://fonts.googleapis.com/css2?family=Lato:wght@400;700&family=Kaushan+Script&display=swap" rel="stylesheet">
<style>
  :root {
    --stage: #e1e2e4;
    --navy: #22266b;
    --slate: #7f9ab3;
    --rule-blue: #3176b5;
    --ink: #4a4a55;
    --paper: #ffffff;
    --edge: #c9cbd0;
  }
  html, body { margin: 0; padding: 0; overflow: hidden; }
  body { width: 1200px; height: 657px; background: var(--stage); position: relative; font-family: "Lato", sans-serif; }

  /* Letterhead */
  .letter {
    position: absolute; left: 41px; top: 62px; width: 379px; height: 533px;
    background: linear-gradient(160deg, #ffffff 40%, #ededee 100%);
    border: 1px solid var(--edge); box-sizing: border-box;
  }
  .brand { position: absolute; display: flex; align-items: center; gap: 7px; }
  .brand-square { background: var(--navy); display: block; }
  .brand-name { color: var(--navy); font-weight: 700; letter-spacing: 1.5px; }
  .letter .brand { left: 21px; top: 18px; }
  .letter .brand-square { width: 22px; height: 22px; }
  .letter .brand-name { font-size: 22px; }

  .letter-rule { position: absolute; top: 61px; height: 2px; background: var(--rule-blue); }
  .letter-rule.long { left: 0; width: 263px; }
  .letter-rule.short { left: 363px; width: 16px; }
  .web { position: absolute; font-size: 9.5px; letter-spacing: 2px; color: #333; }
  .web .accent { color: var(--slate); }
  .letter .web { left: 270px; top: 55px; }

  .letter-body { position: absolute; left: 21px; top: 92px; width: 341px; }
  .salutation { margin: 0 0 3px; font-size: 10px; font-weight: 700; color: var(--navy); }
  .letter-body p.copy { margin: 0 0 9px; font-size: 7.1px; line-height: 11.6px; color: var(--ink); text-align: justify; }
  .closing { position: absolute; left: 21px; top: 420px; font-size: 12px; color: #444; }
  .signature { position: absolute; left: 21px; top: 438px; font-family: "Kaushan Script", cursive; font-size: 19px; color: var(--navy); }
  .letter-footer {
    position: absolute; left: 0; right: 0; top: 516px; display: flex; justify-content: center; gap: 6px;
    font-size: 7.2px; color: #333; align-items: center;
  }
  .letter-footer .sep { color: #aaa; }
  .icon { width: 7px; height: 7px; vertical-align: -1px; margin-right: 2px; }

  /* Envelopes */
  .envelope { position: absolute; width: 563px; height: 251px; background: var(--paper); border: 1px solid var(--edge); box-sizing: border-box; }
  .envelope.back { left: 596px; top: 82px; }
  .envelope.middle { left: 556px; top: 190px; }
  .envelope.front { left: 462px; top: 303px; }
  .flap { position: absolute; left: 0; top: 0; width: 563px; height: 100px; }
  .flap-mark { position: absolute; left: 0; right: 0; text-align: center; font-weight: 700; font-size: 20px; letter-spacing: 2px; }
  .back .flap-mark { top: 34px; color: #ffffff; }
  .middle .flap-mark { top: 38px; color: var(--navy); }

  .front .brand { left: 17px; top: 18px; }
  .front .brand-square { width: 22px; height: 22px; }
  .front .brand-name { font-size: 24px; }
  .front .address { position: absolute; left: 17px; top: 64px; font-size: 10px; color: #222; }
  .front .address .icon { width: 8px; height: 8px; }
  .envelope-rule { position: absolute; top: 234px; height: 1px; background: var(--navy); }
  .envelope-rule.left { left: 0; width: 228px; }
  .envelope-rule.right { left: 335px; right: 0; }
  .front .web { left: 236px; top: 226px; font-size: 10.5px; }
</style>
</head>
<body>

<section class="letter" aria-label="Letterhead">
  <div class="brand"><span class="brand-square"></span><span class="brand-name">TAVRIN</span></div>
  <div class="letter-rule long"></div>
  <div class="web">www.<span class="accent">tavrin</span>.ch</div>
  <div class="letter-rule short"></div>

  <div class="letter-body">
    <p class="salutation">Dear Mr. Lorem,</p>
    <p class="copy">Lorem ipsum dolor sit amet, consectetuer adipiscing elit, sed diam nonummy nibh euismod tincidunt ut laoreet dolore magna aliquam erat volutpat. Ut wisi enim ad minim veniam, quis nostrud exerci tation ullamcorper suscipit lobortis nisl ut aliquip ex ea commodo consequat. Duis autem vel eum iriure dolor in hendiusto odio dignissim qui blandit praesent luptatum zzril delenit facilisi.</p>
    <p class="copy">Lorem ipsum dolor sit amet, consectetuer adipiscing elit, sed diam nonummy nibh euismod tincidunt ut laoreet dolore magna aliquam erat volutpat. Ut wisi enim ad minim veniam, quis nostrud exerci tation ullamcorper suscipit lobortis nisl ut aliquip ex ea commodo consequat.</p>
    <p class="copy">Lorem ipsum dolor sit amet, consectetuer adipiscing elit, sed diam nonummy nibh euismod tincidunt ut laoreet dolore magna aliquam erat volutpat. Ut wisi enim ad minim veniam, quis nostrud exerci tation ullamcorper suscipit lobortis nisl ut aliquip ex ea commodo consequat. Duis autem vel eum iriure dolor in hendiusto odio dignissim qui blandit praesent luptatum zzril delenit facilisi.</p>
    <p class="copy">Lorem ipsum dolor sit amet, consectetuer adipiscing elit, sed diam nonummy nibh euismod tincidunt ut laoreet dolore magna aliquam erat volutpat. Ut wisi enim ad minim veniam, quis nostrud exerci tation ullamcorper suscipit lobortis nisl ut aliquip ex ea commodo consequat.</p>
    <p class="copy">Lorem ipsum dolor sit amet, consectetuer adipiscing elit, sed diam nonummy nibh euismod tincidunt ut laoreet dolore magna aliquam erat volutpat. Ut wisi enim ad minim veniam, quis nostrud exerci tation ullamcorper suscipit lobortis nisl ut aliquip ex ea commodo consequat. Duis autem vel eum iriure dolor in hendiusto odio dignissim qui blandit praesent luptatum zzril delenit facilisi.</p>
    <p class="copy">Lorem ipsum dolor sit amet, consectetuer adipiscing elit, sed diam nonummy nibh euismod tincidunt ut laoreet dolore magna aliquam erat volutpat. Ut wisi enim ad minim veniam, quis nostrud exerci tation ullamcorper suscipit lobortis nisl ut aliquip ex ea commodo consequat.</p>
  </div>

  <div class="closing">Sincerely Your,</div>
  <div class="signature">Your Name</div>

  <div class="letter-footer">
    <span><svg class="icon" viewBox="0 0 10 10"><circle cx="5" cy="5" r="4.3" fill="none" stroke="#22266b" stroke-width="1"/><circle cx="5" cy="4.2" r="1.4" fill="#22266b"/></svg>Lindmattstr. 4, Zip code 9517 Seewil</span>
    <span class="sep">|</span>
    <span><svg class="icon" viewBox="0 0 10 10"><circle cx="5" cy="5" r="4.3" fill="none" stroke="#22266b" stroke-width="1"/><path d="M3.6 3 L4.4 2.8 L5 4.2 L4.4 4.7 Q5 5.9 5.9 6.3 L6.4 5.8 L7.6 6.4 L7.3 7.2 Q4 7.2 3.6 3 Z" fill="#22266b"/></svg>+41 76 555 01 23</span>
    <span class="sep">|</span>
    <span><svg class="icon" viewBox="0 0 10 10"><rect x="1" y="2.5" width="8" height="5.5" fill="#22266b"/><path d="M1 2.5 L5 5.5 L9 2.5" fill="none" stroke="#fff" stroke-width="0.8"/></svg>info@tavrin.ch</span>
  </div>
</section>

<section class="envelope back" aria-label="Envelope back with coloured flap">
  <svg class="flap" viewBox="0 0 563 100" aria-hidden="true">
    <path d="M0,0 L563,0 L556,28 Q549,48 520,54 L300,96 Q281,100 262,96 L43,54 Q14,48 7,28 Z" fill="#7f9ab3"/>
  </svg>
  <div class="flap-mark">TAVRIN</div>
</section>

<section class="envelope middle" aria-label="Envelope back with white flap">
  <svg class="flap" viewBox="0 0 563 100" aria-hidden="true">
    <path d="M0,0 L7,28 Q14,48 43,54 L262,96 Q281,100 300,96 L520,54 Q549,48 556,28 L563,0" fill="none" stroke="#b8bcc4" stroke-width="1"/>
  </svg>
  <div class="flap-mark">TAVRIN</div>
</section>

<section class="envelope front" aria-label="Envelope front">
  <div class="brand"><span class="brand-square"></span><span class="brand-name">TAVRIN</span></div>
  <div class="address"><svg class="icon" viewBox="0 0 10 10"><circle cx="5" cy="5" r="4.3" fill="none" stroke="#22266b" stroke-width="1"/><circle cx="5" cy="4.2" r="1.4" fill="#22266b"/></svg>Lindmattstr. 4, Zip code 9517 Seewil</div>
  <div class="envelope-rule left"></div>
  <div class="web">www.<span class="accent">tavrin</span>.ch</div>
  <div class="envelope-rule right"></div>
</section>

</body>
</html>
```